Zielgruppe
Die Velorin Akademie bietet Kurse, Seminare & Coachings im Bereich der Kommunikation / Persönlichkeitsentwicklung an.
Folgendes Angebot besteht zur Zeit:
Seminare:
- 'Erste Schritte im Dialog', eine Einführung in die Kommunikation.
- 'Heitere Töchter, ruhige Väter' zum Thema Erziehung.
- 'Reifen mit Gelassenheit', zum Thema Älter werden und den Umgang damit.
Kurse:
- 'Gewaltfreie Kommunikation', Übungsgruppe
Coaching:
- Einzelsitzungen mit Hypnose
Ps: im Anhang unter 'Angabot_Vorlage.pdf' finden Sie mehr Infos zu den einezlenen Angebote.
Aufgabenstellung
Bitte berücksichtigen Sie, dass bereits ein Logo besteht (siehe Anhang).
Vom gesamteindruck her sollte die Website aufgeräumt, übersichtlich, harmonisch, freundlich & frisch wirken.
Es wäre super, wenn die Website authentisch wirkt (und weniger '0815 Business Website').
Bitte bedenken Sie, dass die Website sich an Private richtet, die sich nach einem 'strahlenderen & unbeschwerterem Lebene sehnen'.
Wir haben bereits viele Persönlichkeiten stärken können und möchten dies auch witerhin mit viel Herzblut machen.

```html
<!DOCTYPE html>
<html lang="de">
<head>
<meta charset="utf-8">
<title>Velorin Akademie</title>
<link rel="stylesheet" href="https://fonts.googleapis.com/css2?family=Raleway:ital,wght@0,300;0,400;0,500;0,600;0,700;1,300&display=swap">
<style>
:root{
  --page:#ede6e1;
  --panel:#faf8f6;
  --white:#ffffff;
  --muted:#bdb6b5;
  --muted-dark:#a9a2a2;
  --peach:#f3c2a9;
  --peach-soft:#fbe6d8;
  --peach-btn:#fbd2bf;
  --plum:#675770;
  --mauve:#85717c;
  --orange:#f26a3c;
  --bar:#e3ddd7;
}
*{box-sizing:border-box;margin:0;padding:0}
html,body{width:1200px;height:3561px;overflow:hidden}
body{background:var(--page);font-family:'Raleway',sans-serif;color:var(--muted);position:relative}
.abs{position:absolute}
.hero{left:134px;top:79px;width:939px;height:547px;overflow:hidden}
.hero-photo{position:absolute;inset:0;background:radial-gradient(ellipse at 50% 85%,#f4e7dc 0%,#d9cfd8 30%,#b7bbd0 60%,#a7b0c7 100%)}
.hero-shade{position:absolute;inset:0;background:rgba(255,255,255,.35)}
.topbar{position:absolute;left:0;top:0;width:100%;height:55px;background:rgba(240,240,244,.85)}
.brand-small{position:absolute;left:24px;top:20px;font-size:11px;font-weight:500;letter-spacing:2px;color:#a7a5ad}
.nav{position:absolute;top:25px;font-size:8px;letter-spacing:1px;color:#b9b5bd}
.nav-line{position:absolute;left:695px;top:40px;width:75px;height:1px;background:#e9c9c0}
.hero-title{position:absolute;left:0;width:100%;top:335px;text-align:center;color:#fff;font-size:36px;font-weight:400;letter-spacing:7px}
.hero-sub{position:absolute;left:0;width:100%;top:393px;text-align:center;color:#fff;font-size:18px;letter-spacing:2px;font-weight:500}
.dots{position:absolute;left:452px;top:523px;display:flex;gap:6px}
.dots span{width:7px;height:7px;border-radius:50%;border:1px solid #fff}
.dots span.on{background:#fff}
.newsletter{left:134px;top:643px;width:939px;height:61px;background:var(--peach-soft);border-left:2px solid #f3c9b2}
.newsletter .lead{position:absolute;left:137px;top:15px;font-size:12px;letter-spacing:1px;color:#fff;font-weight:600;line-height:16px}
.newsletter .lead span{font-weight:400;letter-spacing:0}
.newsletter .field{position:absolute;left:408px;top:16px;width:328px;height:30px;background:#fff;font-size:9px;letter-spacing:1px;padding:10px 12px;color:#d3cbc8}
.newsletter .ok{position:absolute;left:752px;top:20px;width:38px;height:22px;background:var(--peach-btn);color:#fff;font-size:9px;text-align:center;line-height:22px;font-weight:600}
.intro{left:134px;top:704px;width:939px;height:149px;background:var(--white)}
.intro h1{position:absolute;width:100%;top:75px;text-align:center;font-weight:400;font-size:26px;letter-spacing:1px;color:#c5c0c1}
.offer{left:134px;width:939px;background:var(--panel)}
.photo{position:absolute}
.offer-title{position:absolute;left:378px;font-size:17px;font-weight:600;color:#c9c3c3}
.facts{position:absolute;left:378px;font-size:12.5px;font-weight:700;color:var(--peach)}
.facts div{height:32.3px}
.facts b{display:inline-block;width:81px;font-weight:600}
.btn{position:absolute;background:var(--peach-btn);color:#fff;font-size:10px;letter-spacing:1.5px;text-align:center;font-weight:500}
.text{position:absolute;left:50px;width:792px;font-size:10.5px;line-height:14.5px;font-weight:300}
.text.it{font-style:italic}
.agenda-h{position:absolute;left:50px;font-size:16px;font-weight:500;color:#b7b1b1}
.agenda-row{position:absolute;left:50px;font-size:11px;line-height:14.5px;font-weight:300}
.agenda-row .k{position:absolute;left:0;top:0;color:var(--peach);font-weight:500;letter-spacing:.5px;white-space:nowrap}
.agenda-row .v{position:absolute;white-space:nowrap}
.modal{left:326px;top:1807px;width:582px;height:505px;background:var(--mauve);box-shadow:2px 3px 8px rgba(0,0,0,.25)}
.modal-head{position:absolute;left:0;top:0;width:100%;height:94px;background:var(--plum)}
.modal-head h2{position:absolute;width:100%;top:36px;text-align:center;color:#fff;font-weight:500;font-size:26px;letter-spacing:1.5px}
.modal-close{position:absolute;left:558px;top:9px;color:#fff;font-size:14px;font-weight:300}
.modal-facts{position:absolute;left:115px;top:113px;color:#fff;font-size:12.5px;font-weight:600}
.modal-facts div{height:26.5px}
.modal-facts b{display:inline-block;width:80px;font-weight:600}
.modal-sep{position:absolute;left:0;top:228px;width:100%;height:22px;background:var(--plum)}
.modal-foot{position:absolute;left:0;top:401px;width:100%;height:104px;background:var(--plum)}
.input{position:absolute;background:#fff;font-size:10px;letter-spacing:1px;color:#6b6070;padding:11px 15px}
.modal-btn{position:absolute;left:205px;top:33px;width:164px;height:33px;background:var(--orange);color:#fff;font-size:11px;letter-spacing:1.5px;text-align:center;line-height:33px;font-weight:500}
.landscape{left:134px;top:2795px;width:939px;height:260px;background:linear-gradient(180deg,#ece9ea 0%,#e7e1de 55%,#d9d2cf 100%)}
.footer{left:134px;top:3055px;width:939px;height:349px;background:var(--white)}
.footer .center{position:absolute;left:0;width:330px;text-align:center}
.foot-brand{top:118px;font-size:15px;letter-spacing:3px;color:#b9b3b3}
.foot-co{top:180px;font-size:11.5px;font-weight:600;letter-spacing:1px;color:#c2bcbc}
.foot-addr{top:212px;font-size:12px;line-height:16px;color:#c9c3c3}
.foot-tel{top:261px;font-size:12px;line-height:16px;color:#c9c3c3}
.contact-h{position:absolute;left:490px;top:38px;font-size:11.5px;letter-spacing:1px;line-height:14px;color:#c2bcbc}
.cin{position:absolute;left:490px;width:329px;border:1px solid #e6d8d2;font-size:9px;letter-spacing:1px;color:#d7cdca;padding:10px 11px}
.bottom{left:134px;top:3404px;width:939px;height:80px;background:var(--bar);border-left:3px solid #bcae9f}
.bottom span{position:absolute;top:37px;font-size:11.5px;letter-spacing:.5px;color:#fff}
</style>
</head>
<body>

<header class="abs hero">
  <div class="hero-photo" role="img" aria-label="Sternenhimmel mit Milchstrasse über Berghängen, kleine Gruppe mit erhobenen Armen auf einem Gipfel"></div>
  <div class="hero-shade"></div>
  <div class="topbar">
    <div class="brand-small">Velorin Akademie</div>
    <span class="nav" style="left:658px">HOME</span>
    <span class="nav-line"></span>
    <span class="nav" style="left:783px">KONTAKT</span>
    <span class="nav" style="left:850px">ÜBER UNS</span>
  </div>
  <div class="hero-title">VELORIN AKADEMIE</div>
  <div class="hero-sub">NEUE PERSPECTIVEN · NEUE HORIZONTE</div>
  <svg class="abs" style="left:22px;top:262px" width="20" height="40" viewBox="0 0 20 40"><path d="M18 2 L3 20 L18 38" fill="none" stroke="#fff" stroke-width="1.5"/></svg>
  <svg class="abs" style="left:898px;top:262px" width="20" height="40" viewBox="0 0 20 40"><path d="M2 2 L17 20 L2 38" fill="none" stroke="#fff" stroke-width="1.5"/></svg>
  <div class="dots"><span></span><span class="on"></span><span></span></div>
</header>

<section class="abs newsletter">
  <div class="lead">KOSTENLOSES ERSTGESPRÄCH<br><span>Abonnieren Sie unseren Newsletter!</span></div>
  <div class="field">E-MAIL ADRESSE</div>
  <div class="ok">OK</div>
</section>

<section class="abs intro"><h1>UNSERE AKTUELLE ANGEBOTE</h1></section>

<section class="abs offer" style="top:853px;height:906px">
  <div class="photo" role="img" aria-label="Schwarzweissfoto einer Familie, die über eine Brücke spaziert" style="left:50px;top:46px;width:272px;height:246px;background:linear-gradient(135deg,#d6d6d6,#ebebeb 60%,#dcdcdc)"></div>
  <div class="offer-title" style="top:45px">SEMINAR: Heitere Töchter, ruhige Väter</div>
  <div class="facts" style="top:86px">
    <div><b>ZIEL</b>Entspanntes und erfülltes Leben mit Kinder</div>
    <div><b>DAUER</b>4 Abende à 1,5 Stunden</div>
    <div><b>KOSTEN</b>CHF 280.-</div>
    <div><b>ORT</b>Basel, Rialto</div>
    <div><b>DATUM</b>7-11. Mai 2019.</div>
  </div>
  <div class="btn" style="left:378px;top:261px;width:125px;height:31px;line-height:31px">ANMELDEN</div>
  <p class="text it" style="top:339px">„Unter Erziehung versteht man die pädagogische Einflussnahme auf die Entwicklung und das Verhalten Heranwachsender.“ Erziehungstheorien gibt es unzählige, die das Spektrum von streng und autoritär bis hin zum Laisser-faire decken. Das selbst erlebte wird z.T. auch unreflektiert wiederholt und/oder wir verlieren uns in unzählige Ratgeber.</p>
  <p class="text" style="top:400px">Mithilfe der Neurowissenschaften wird uns klar, dass das oft kräftezehrende Ringen rund um die Erziehung absolut unnötig und überflüssig ist, ja sogar schädigend. Am wirksamsten und effektivsten begleiten wir die Entwicklung eines Kindes mit Beziehung und Selbst-Erziehung – das ist die magische Formel. Indem wir zu nachahmenswerten Erwachsenen werden, fördern wir unsere eigene Persönlichkeitsentwicklung und ermöglichen damit eine harmonische, authentische und unterstützende Umgebung für die Kinder. Im 2. Teil gehen wir der Frage nach, wie Eltern ihre Kindern verhelfen zu starken, selbstsicheren und erfüllten Erwachsenen zu werden, die ihren eigenen Platz in der Gesellschaft kreieren – jenseits von Konkurrenzkampf und Studiumsinflation.</p>
  <div class="agenda-h" style="top:533px">AGENDA</div>
  <div class="agenda-row" style="top:574px"><span class="k">1. ABEND</span><span class="v" style="left:87px">• Ruhig ankommen und zuhören<br>• Was Kinder wirklich brauchen<br>• Eigene Muster aus der Kindheit erkennen und liebevoll betrachten lernen.</span></div>
  <div class="agenda-row" style="top:636px"><span class="k">2. ABEND</span><span class="v" style="left:89px">• Beziehung statt Erziehung<br>• Grenzen setzen ohne Druck<br>• Vorbild sein im Alltag<br>• Kleine Übungen für zu Hause, die Nähe schaffen und Vertrauen stärken.</span></div>
  <div class="agenda-row" style="top:710px"><span class="k">3. ABEND</span><span class="v" style="left:91px">• Gefühle benennen und annehmen<br>• Streit als Chance<br>• Gelassen bleiben im Trubel</span></div>
  <div class="agenda-row" style="top:773px"><span class="k">4. ABEND</span><span class="v" style="left:91px">• Starke Kinder begleiten<br>• Den eigenen Weg finden<br>• Rückblick und nächste Schritte: wie wir das Gelernte lebendig halten.</span></div>
  <div class="btn" style="left:404px;top:854px;width:126px;height:31px;line-height:31px">ANMELDEN</div>
</section>

<section class="abs offer" style="top:1797px;height:947px">
  <div class="photo" role="img" aria-label="Nahaufnahme einer Armbanduhr" style="left:53px;top:51px;width:180px;height:244px;background:linear-gradient(135deg,#cfcfcf,#ededed 70%)"></div>
  <div class="offer-title" style="left:780px;top:89px;font-size:12.5px;color:var(--peach);font-weight:700">Deinem Leben“</div>
  <p class="text" style="top:339px">Zeit ist ein allgegenwärtiges Thema und doch fehlt sie uns ständig. Was ist sie eigentlich und haben wir sie jemals? Wie und wo nehmen wir uns Zeit für das, was uns wirklich wichtig ist und für einen bewussten Ausstieg aus der Eile – könnten? Mit welchen Folgen?</p>
  <p class="text" style="top:384px">Wir setzen uns mit unseren eigenen Vorstellungen von Zeit auseinander und stellen sie den Erkenntnissen der Wissenschaften gegenüber. Aus der passiven Haltung wird eine aktive.</p>
  <p class="text it" style="top:420px">„Älter werden ist unumgänglich, alt sein nicht.“</p>
  <div class="agenda-h" style="top:498px">AGENDA</div>
  <div class="agenda-row" style="top:537px"><span class="k">1. BLOCK</span><span class="v" style="left:120px">08:00 - 10:00<br>Was ist Zeit? Die Erfindung der Zeit.<br>Wie hat dieser begriff unser Bewusstsein geprägt, mit welchen Folgen?</span></div>
  <div class="agenda-row" style="top:599px"><span class="k">2. BLOCK</span><span class="v" style="left:121px">10:00-12:00<br>Wo finden wir aus der Zeit heraus? Wo gibt es keine Zeit?<br>Praktische Übung – Achtsamkeit</span></div>
  <div class="agenda-row" style="top:660px"><span class="k">MITTAGSPAUSE</span><span class="v" style="left:121px">12:00 - 13:30</span></div>
  <div class="agenda-row" style="top:714px"><span class="k">3. BLOCK</span><span class="v" style="left:118px">13:30 - 15:30<br>Bezug von Zeit und Alter – unsere Vorstellungen wahrnehmen.<br>Ist altern ein naturgegebener Prozess dem wir unterworfen sind oder können wir es steuern? Wir gehen der Frage nach,<br>wie eine differenzierte und bewusst gewählte Auffassung von Zeit und älter werden sich auswirken.</span></div>
  <div class="agenda-row" style="top:784px"><span class="k">4. BLOCK</span><span class="v" style="left:118px">15:30 - 17:00<br>Bahnbrechende Aussichten.<br>Fazit: Für welches altern entscheiden wir uns?<br>Dankbarkeit und Fülle</span></div>
  <div class="btn" style="left:404px;top:886px;width:126px;height:31px;line-height:31px">ANMELDEN</div>
</section>

<div class="abs modal" role="dialog" aria-label="Anmeldungsformular">
  <div class="modal-head"><h2>ANMELDUNGSFORMULAR</h2><span class="modal-close">X</span></div>
  <div class="modal-facts">
    <div><b>SEMINAR</b>Zeit und Alternativen</div>
    <div><b>KOSTEN</b>CHF 280.-</div>
    <div><b>ORT</b>Schloss Talheim</div>
    <div><b>DATUM</b>11. Mai 2019.</div>
  </div>
  <div class="modal-sep"></div>
  <div class="input" style="left:43px;top:283px;width:225px;height:32px">NAME</div>
  <div class="input" style="left:313px;top:283px;width:225px;height:32px">VORNAME</div>
  <div class="input" style="left:43px;top:332px;width:495px;height:32px">E-MAIL ADRESSE</div>
  <div class="modal-foot"><div class="modal-btn">ANMELDEN</div></div>
</div>

<div class="abs landscape" role="img" aria-label="Person sitzt im Dunst auf einem Felsvorsprung über einer Berglandschaft"></div>

<footer class="abs footer">
  <div class="center foot-brand">VELORIN AKADEMIE</div>
  <div class="center foot-co">VELORIN AKADEMIE GMBH.</div>
  <div class="center foot-addr">Wiesenstr. 17<br>4102 Talheim</div>
  <div class="center foot-tel">TEL: 061 555 01 23<br>info@velorinakademie.ch</div>
  <div class="contact-h">NOCH FRAGEN, ANREGUNGEN?<br>SCHREIBEN SIE UNS!</div>
  <div class="cin" style="top:79px;height:31px">NAME</div>
  <div class="cin" style="top:125px;height:30px">E-MAIL ADRESSE</div>
  <div class="cin" style="top:166px;height:101px">NACHRICHT</div>
  <div class="btn" style="left:490px;top:284px;width:163px;height:33px;line-height:33px">SENDEN</div>
</footer>

<div class="abs bottom">
  <span style="left:54px">Datenschutz</span>
  <span style="left:174px">Impressum</span>
  <span style="left:395px">VELORIN AKADEMIE | 2019</span>
</div>

</body>
</html>
```